Business Card - high end, modern health care

Hey designers!

We need a double sided business card for the boutique, cutting edge physical therapy rehabilitation centre in Sydney's Northern Beaches.

With the most qualified physios in the area The Harbourview Motion Clinic does what other physiotherapy practices do not, we take our time with our patients giving them longer appointments, better physios and therefor faster results!

We guarantee that the service people receive at THMC will be unparalleled.

Hence we need a business card to reflect our modern, boutique, high end service. The final design needs to reflect that we are in a class of our own yet with the feel of beachside retreat.

Below I have attached our logo in both blue on white and white on blue. The exact colour is;
and the font that we have used in our logo is Tex Gyre Aventador.

I like the idea of the blue as the main colour as it is more eye catching and our signage onto the main road will be in this blue and in the interest of consistency across marketing the blue needs to be a part of the design. However I would appreciate a few designs onto a wooden background as this is a visual theme within the fitout of the practice.

The design needs to be of standard size (91x55mm).

Target Market(s)

We target people who have an end outcome in mind and those who have had poor experiences with other providers and ensure that everyone gets the care that they deserve with a premium service that is tailored to the individuals circumstances. As a premium service, the target market is highly educated, business and tech savvy with the additional target market of elderly people who have self funded their retirement and see value in paying for the best ongoing rehabilitation to maintain independence.

Industry/Entity Type

Physical Therapy

Contact Information for Business Card

Name, designation( Titled Musculoskeletal Physiotherapist... there will also be those in the company that have multiple designations ie 5 or 6 words long), phone number, email, facebook, instagram, address

Font styles to use
Sans Serif

Colors

Designer to choose colors to be used in the design.

Requirements
Must have
• Front - The logo as large as possible, blue or wooden theme, and all of the important details.
• Back - A blank space/lines on which to write appointment times (no "Appointment, date, time" etc.)
Nice to have
• facebook url
• logos for facebook and instagram
• Mini logos for the phone and email?

```html
<!DOCTYPE html>
<html lang="en">
<head>
<meta charset="utf-8">
<title>The Harbourview Motion Clinic – Business Card</title>
<link rel="stylesheet" href="https://fonts.googleapis.com/css2?family=Montserrat:wght@600&display=swap">
<style>
  :root {
    --brand-blue: #1057a5;
    --paper-white: #ffffff;
    --wood-light: #f3d9a6;
    --wood-mid: #e8c283;
    --wood-dark: #d9a862;
  }
  html, body {
    margin: 0;
    padding: 0;
    width: 1200px;
    height: 726px;
    overflow: hidden;
    background: var(--paper-white);
  }
  .business-card {
    position: relative;
    width: 1200px;
    height: 726px;
    overflow: hidden;
    background: var(--paper-white);
    font-family: "Montserrat", sans-serif;
  }
  .brand-field {
    position: absolute;
    inset: 0;
    width: 1200px;
    height: 726px;
  }
  .brand-field .wave { fill: var(--brand-blue); }
  .brand-name {
    fill: var(--paper-white);
    font-family: "Montserrat", sans-serif;
    font-weight: 600;
  }
  .wood-panel {
    position: absolute;
    left: 0;
    top: 502px;
    width: 1200px;
    height: 224px;
    background: linear-gradient(180deg, var(--wood-mid) 0%, var(--wood-light) 35%, var(--wood-mid) 70%, var(--wood-light) 100%);
  }
  .contact-icon {
    position: absolute;
    width: 60px;
    height: 60px;
    border-radius: 50%;
    background: var(--brand-blue);
  }
  .contact-icon svg {
    position: absolute;
    inset: 0;
    width: 60px;
    height: 60px;
  }
  .icon-social-a { left: 43px; top: 552px; }
  .icon-social-b { left: 43px; top: 627px; }
  .icon-email { left: 709px; top: 552px; }
  .icon-phone { left: 710px; top: 628px; }
</style>
</head>
<body>
  <main class="business-card">
    <svg class="brand-field" viewBox="0 0 1200 726" aria-hidden="false">
      <path class="wave wave-main" d="M0,76 C180,15 420,28 640,70 C850,110 1050,140 1200,152 V502 H0 Z"/>
      <path class="wave wave-crest" d="M512,20 C800,62 1060,80 1200,44 V108 C1000,112 760,72 512,20 Z"/>
      <circle class="brand-mark" cx="184" cy="242" r="86" fill="#ffffff"/>
      <text class="brand-name brand-name-top" x="290" y="260" font-size="84" textLength="794" lengthAdjust="spacingAndGlyphs">THE HARBOURVIEW</text>
      <text class="brand-name brand-name-sub" x="296" y="328" font-size="62" textLength="786" lengthAdjust="spacing">MOTION CLINIC</text>
    </svg>

    <div class="wood-panel" role="img" aria-label="Light timber wood-grain background"></div>

    <div class="contact-icon icon-social-a" aria-label="Social profile"></div>
    <div class="contact-icon icon-social-b" aria-label="Social profile"></div>

    <div class="contact-icon icon-email" aria-label="Email">
      <svg viewBox="0 0 60 60">
        <rect x="14" y="19" width="32" height="22" rx="2" fill="none" stroke="#ffffff" stroke-width="3"/>
        <path d="M15,21 L30,33 L45,21" fill="none" stroke="#ffffff" stroke-width="3" stroke-linejoin="round"/>
        <path d="M15,40 L25,30 M45,40 L35,30" fill="none" stroke="#ffffff" stroke-width="2.5"/>
      </svg>
    </div>

    <div class="contact-icon icon-phone" aria-label="Phone">
      <svg viewBox="0 0 60 60">
        <path d="M21,15 l6,7 c1,1.2 0.8,2.6 -0.3,3.6 l-2.5,2.2 c2,4 5,7.2 9,9.4 l2.3,-2.4 c1,-1 2.5,-1.2 3.6,-0.3 l7,5.7 c1.2,1 1.2,2.6 0.2,3.7 l-3,3 c-2,2 -5,2.4 -7.6,1 C27,44 17,34 12.6,25.6 c-1.3,-2.6 -1,-5.6 1,-7.6 l3.6,-3.2 c1.1,-0.9 2.7,-0.9 3.8,0.2 Z" fill="#ffffff"/>
      </svg>
    </div>
  </main>
</body>
</html>
```